Redesign company trifold brochure

We are rebranding our company in September and looking for a more professional design for our brochure.

What we do - providing interdisciplinary care for those supporting ill, elderly and special needs pets at home following the human hospice model of care - is very novel and our brochure is key in explaining it and our offerings.

We serve dogs and cats. Most of the animals are quite sick, elderly. I have many personal and stock photos we can use in the brochure. Please - no pictures of puppies and/or kittens.

The hard part is fitting the info and message into a clear and concise format.

It must be appealing both to pet owners and vets (who are our primary source of patients through referrals).

It should covey WARMTH, COMPASSION, PROFESSIONALISM, and EXPERTISE.

Please look at our website www.TrellisAnimalRespite.com for more info

We have until now used maroon and copper for colors - to reflect the "sunset" of the pets life. BUT are now changing to Navy, Teal and White to reflect calm, trust and competence.

We will use the same logo recolored.

Existing brochure and new logo are attached.

PLEASE ask questions!!
Updates

We have a library of stock images you are welcome to use. All have been legally acquired and we have the right to use them. You DO NOT have to use them, just sending along in case you wish to. https://www.filecrate.example/sh/qk4vrm82zd1pyno/KLQ7Ztbn-Rrfx2mh9sWpYJ4Dc?dl=0

Our colors are NAVY, TEAL and WHITE. For your reference, the navy we use is 99/87/44/55 (CMYK) The Teal we use is 76/11/44/0 (CMYK) Thank you!

Designers -- pleaseuse pictures of older pets (no puppies or kittens). Below is a link to stock photos we own that would be appropriate for use in the brochure. https://www.filecrate.example/sh/w274m6t9pxkr5da/KLRn3GsfwlTVBXEPcq_8ZNj5u?dl=0 THANK YOU!

Designers -- I would VERY much like to include a photo of a pet in a wheel chair. I have personal photos as well as (purchased) stock photos for this purpose which can be found at http://lnk.example/TARHC-Pets-in-Wheelchairs Thank you!!

Today is the last day! Many of you have submitted beautiful designs and others are rolling in. I am so appreciative of your time and energy!! Please do not let the deadline pass without YOUR very BEST entry being submitted!! Thank you! - Miriam & All of us at Trellis Animal Respite & Home Care

Target Market(s)

Pet Owners and Veterinarians

Industry/Entity Type

Pet Care

Font styles to use
Serif

Colors
0455a3
33b8a4
ffffff

Requirements
Must have
• Our logo and information about our services. Pictures of pets. Our contact info. PLEASE NOTE: this is a 2 sided brochure. Please submit both inside and outside.
Should not have
• puppies, kittens - anything off message

```html
<!DOCTYPE html>
<html lang="en">
<head>
<meta charset="utf-8">
<title>Trellis Animal Respite &amp; Home Care – Trifold Brochure</title>
<link href="https://fonts.googleapis.com/css2?family=Lato:ital,wght@0,400;0,700;0,900;1,700&display=swap" rel="stylesheet">
<style>
  :root{
    --navy:#0c2150;
    --navy-deep:#081837;
    --teal:#1fa59a;
    --teal-light:#33b8a4;
    --white:#ffffff;
    --ink:#3a4657;
    --page:#e6e8eb;
    --fur-gold:#c99a52;
    --fur-cream:#e9d6b4;
    --grass:#7f9a4a;
  }
  *{box-sizing:border-box;margin:0;padding:0}
  html,body{width:783px;height:1200px;overflow:hidden}
  body{background:var(--page);font-family:"Lato",Arial,sans-serif;color:var(--ink);position:relative}
  .spread{position:absolute;left:40px;width:703px;height:548px;background:var(--white);overflow:hidden;box-shadow:0 3px 10px rgba(0,0,0,.25)}
  .spread--outside{top:28px}
  .spread--inside{top:612px}
  .panel{position:absolute;top:0;width:234.33px;height:548px;overflow:hidden}
  .panel--1{left:0}.panel--2{left:234.33px}.panel--3{left:468.66px}
  .panel-art{position:absolute;inset:0;width:100%;height:100%}
  .photo{position:absolute}

  /* outside – beliefs */
  .beliefs{background:var(--navy)}
  .beliefs h2{position:absolute;left:18px;top:18px;font-size:13px;font-weight:900;color:var(--teal-light);letter-spacing:.3px}
  .beliefs ul{position:absolute;left:18px;top:42px;width:200px;list-style:none}
  .beliefs li{position:relative;padding-left:10px;font-size:7.6px;line-height:1.3;color:var(--white);margin-bottom:4px}
  .beliefs li::before{content:"";position:absolute;left:0;top:3px;width:4px;height:4px;border-radius:50%;background:var(--teal-light)}

  /* outside – contact */
  .contact{background:var(--white)}
  .brand{display:flex;align-items:center;gap:7px;font-weight:700;color:var(--navy);line-height:1.15}
  .brand-dot{flex:none;width:16px;height:16px;border-radius:50%;background:var(--teal)}
  .contact .brand{position:absolute;left:30px;top:258px;width:180px;font-size:11px}
  .contact-list{position:absolute;left:30px;top:316px;list-style:none}
  .contact-list li{display:flex;gap:7px;font-size:8.2px;font-weight:700;color:var(--navy);line-height:1.3;margin-bottom:8px}
  .contact-list svg{flex:none;width:10px;height:10px;margin-top:1px}
  .url-tab{position:absolute;left:16px;right:16px;bottom:12px;height:34px;border-radius:12px 12px 0 0;background:var(--navy);color:var(--white);font-size:8.6px;font-weight:700;display:flex;align-items:center;justify-content:center}

  /* outside – cover */
  .cover{background:var(--navy)}
  .cover .brand{position:absolute;left:30px;top:400px;width:180px;font-size:13px;color:var(--white)}
  .cover .brand-dot{width:20px;height:20px;background:var(--teal-light)}
  .url-pill{position:absolute;left:18px;right:18px;bottom:14px;height:30px;border-radius:15px;background:var(--teal);color:var(--white);font-size:8.6px;font-weight:700;display:flex;align-items:center;justify-content:center}

  /* inside – palliative */
  .palliative h2{position:absolute;left:0;right:0;top:266px;text-align:center;font-size:12.5px;font-weight:900;color:var(--navy);line-height:1.25}
  .palliative .copy{position:absolute;left:18px;width:200px;top:306px}
  .palliative p{font-size:7.6px;line-height:1.35;margin-bottom:7px}
  .term{color:var(--teal);font-weight:900}
  .sub-head{font-size:8.6px;font-style:italic;font-weight:700;color:var(--navy);margin:4px 0 6px}
  .bullets{list-style:none}
  .bullets li{position:relative;padding-left:10px;font-size:7.6px;line-height:1.3;margin-bottom:4px}
  .bullets li::before{content:"";position:absolute;left:0;top:3px;width:4px;height:4px;border-radius:50%;background:var(--teal)}
  .url-pill--navy{background:var(--navy);left:16px;right:42px;bottom:14px}

  /* inside – services */
  .services h2{position:absolute;left:14px;top:196px;font-size:11.5px;font-weight:900;color:var(--navy)}
  .services .copy{position:absolute;left:14px;width:206px;top:216px}
  .services p{font-size:7.3px;line-height:1.33;margin-bottom:6px}
  .services .bullets li{font-size:7.3px;margin-bottom:3.2px}
  .badge{position:absolute;left:48px;top:10px;width:150px;height:140px}

  /* inside – team */
  .team{background:var(--teal)}
  .team h3{position:absolute;left:14px;top:14px;width:200px;font-size:8.6px;font-style:italic;font-weight:900;color:var(--navy);line-height:1.25}
  .skills{position:absolute;left:14px;top:44px;width:210px;display:flex;gap:12px}
  .skills ul{list-style:none;flex:1}
  .skills li,.team-list li{position:relative;padding-left:10px;font-size:7.4px;line-height:1.28;color:var(--white);margin-bottom:4px}
  .skills li::before,.team-list li::before{content:"";position:absolute;left:0;top:3px;width:4px;height:4px;border-radius:50%;background:var(--white)}
  .team h2{position:absolute;left:0;right:0;top:190px;text-align:center;font-size:12px;font-weight:900;color:var(--navy)}
  .team .lead{position:absolute;left:14px;top:212px;width:206px;font-size:8.4px;font-style:italic;font-weight:900;color:var(--navy);line-height:1.3}
  .team-list{position:absolute;left:14px;top:248px;width:206px;list-style:none}
</style>
</head>
<body>

<!-- OUTSIDE -->
<section class="spread spread--outside">

  <div class="panel panel--1 beliefs">
    <svg class="panel-art" viewBox="0 0 234 548" preserveAspectRatio="none" aria-hidden="true">
      <path d="M234 170 C170 250 90 300 0 330 L0 548 L234 548 Z" fill="#0d2a5c"/>
      <path d="M234 200 C180 270 100 320 0 355 L0 400 C110 360 190 300 234 240 Z" fill="var(--teal)"/>
    </svg>
    <h2>WE BELIEVE</h2>
    <ul>
      <li>That animals are conscious beings, capable of thought, feeling, emotion and choice</li>
      <li>That each animal is an individual with his or her unique needs and wishes</li>
      <li>That all pets deserve to be pain-free</li>
      <li>That the principles of human hospice and palliative care are equally powerful when applied to animals</li>
      <li>That an interdisciplinary team is essential to addressing the needs of pets and their families through aging and illness</li>
      <li>That quality of life is subjective, best evaluated by the family who knows and loves the animal</li>
      <li>That there isn't one answer that is right for every animal or every family</li>
    </ul>
    <div class="photo" role="img" aria-label="Photo of a sitting terrier-mix dog" style="left:20px;top:270px;width:150px;height:262px;border-radius:40% 40% 10% 10%;background:radial-gradient(ellipse at 50% 35%,#f2eee8 0%,#d9c7aa 45%,rgba(120,90,60,.0) 75%)"></div>
  </div>

  <div class="panel panel--2 contact">
    <svg class="panel-art" viewBox="0 0 234 548" preserveAspectRatio="none" aria-hidden="true">
      <path d="M0 0 L40 0 C30 60 0 110 0 120 Z" fill="var(--teal)"/>
      <path d="M0 232 L234 232 L234 140 C150 180 70 220 0 232 Z" fill="#eef2f4"/>
    </svg>
    <div class="photo" role="img" aria-label="Photo of a black Labrador in grass, framed in a circle" style="left:24px;top:14px;width:130px;height:130px;border-radius:50%;border:5px solid var(--teal);background:radial-gradient(circle at 50% 45%,#2a2a2a 0%,#3b3b30 35%,var(--grass) 70%)"></div>
    <div class="photo" role="img" aria-label="Photo of a tabby cat lying down" style="left:0;top:150px;width:234px;height:82px;clip-path:polygon(0 40%,100% 0,100% 100%,0 100%);background:linear-gradient(90deg,#cfc9c0,#8e7a63 45%,#c8bfb2)"></div>
    <div class="brand"><span class="brand-dot"></span><span>Trellis Animal Respite &amp; Home Care</span></div>
    <ul class="contact-list">
      <li><svg viewBox="0 0 10 10"><path d="M2 1 L4 1 L4.6 3 L3.4 3.8 C4 5.2 4.8 6 6.2 6.6 L7 5.4 L9 6 L9 8 C9 8.6 8.6 9 8 9 C4.2 8.8 1.2 5.8 1 2 C1 1.4 1.4 1 2 1Z" fill="var(--teal)"/></svg><span>(555) 302-TARH</span></li>
      <li><svg viewBox="0 0 10 10"><path d="M5 1 L9.5 5 L8.3 5 L8.3 9 L6 9 L6 6.5 L4 6.5 L4 9 L1.7 9 L1.7 5 L0.5 5 Z" fill="var(--teal)"/></svg><span>218 Alder Lane Suite 40<br>Brookfield, MA 01506</span></li>
      <li><svg viewBox="0 0 10 10"><rect x="1" y="2" width="8" height="6" fill="var(--teal)"/><path d="M1 2 L5 5.5 L9 2" stroke="#fff" stroke-width=".9" fill="none"/></svg><span>info@TrellisAnimalRespite.com</span></li>
    </ul>
    <div class="url-tab">www.TrellisAnimalRespite.com</div>
  </div>

  <div class="panel panel--3 cover">
    <div class="photo" role="img" aria-label="Photo of a smiling golden retriever in a garden" style="left:0;top:0;width:234px;height:330px;background:radial-gradient(ellipse at 55% 45%,#f0dcae 0%,var(--fur-gold) 35%,#6f7f3c 70%,#3e5124 100%)"></div>
    <svg class="panel-art" viewBox="0 0 234 548" preserveAspectRatio="none" aria-hidden="true">
      <path d="M0 250 C80 330 160 340 234 300 L234 548 L0 548 Z" fill="var(--navy)"/>
      <path d="M0 250 C80 330 160 340 234 300 L234 318 C160 358 80 348 0 268 Z" fill="var(--teal)"/>
      <path d="M0 0 L0 230 C10 150 20 80 60 0 Z" fill="var(--navy)" opacity=".9"/>
    </svg>
    <div class="brand"><span class="brand-dot"></span><span>Trellis Animal Respite &amp; Home Care</span></div>
    <div class="url-pill">www.TrellisAnimalRespite.com</div>
  </div>
</section>

<!-- INSIDE -->
<section class="spread spread--inside">

  <div class="panel panel--1 palliative">
    <div class="photo" role="img" aria-label="Photo of a golden retriever sitting on a lawn" style="left:0;top:0;width:234px;height:250px;background:radial-gradient(ellipse at 40% 45%,#f1d7a0 0%,var(--fur-gold) 35%,#8aa257 70%,#5f7a33 100%)"></div>
    <svg class="panel-art" viewBox="0 0 234 548" preserveAspectRatio="none" aria-hidden="true">
      <path d="M0 255 C90 250 170 220 234 150 L234 548 L0 548 Z" fill="var(--white)"/>
      <path d="M0 240 C90 236 170 205 234 135 L234 150 C170 220 90 250 0 255 Z" fill="var(--navy)"/>
    </svg>
    <h2>PALLIATIVE CARE<br>AND HOSPICE</h2>
    <div class="copy">
      <p><span class="term">PALLIATIVE CARE</span> seeks to relieve suffering and improve quality of life at all stages of illness, injury and disease, whether curable or not.</p>
      <p><span class="term">HOSPICE</span> a special kind of Palliative Care focused on those with a life expectancy of less than one year.</p>
      <h3 class="sub-head">BOTH PALLIATIVE CARE AND HOSPICE</h3>
      <ul class="bullets">
        <li>Focus on living fully</li>
        <li>Recognize and address all suffering – physical, emotional, social and spiritual</li>
        <li>Use a team approach to meet the needs of the animal and his or her family</li>
        <li>Affirm life while viewing death as a natural, normal process</li>
      </ul>
    </div>
    <div class="url-pill url-pill--navy">www.TrellisAnimalRespite.com</div>
  </div>

  <div class="panel panel--2 services">
    <svg class="panel-art" viewBox="0 0 234 548" preserveAspectRatio="none" aria-hidden="true">
      <path d="M0 150 C60 130 150 80 234 0 L234 14 C150 94 60 146 0 166 Z" fill="var(--navy)"/>
    </svg>
    <svg class="badge" viewBox="0 0 150 140" aria-hidden="false" role="img" aria-label="We are here for you 24 hours a day, every day of the year">
      <defs><path id="arc" d="M75 8 A62 62 0 0 1 75 132"/></defs>
      <circle cx="60" cy="70" r="54" fill="var(--teal)"/>
      <circle cx="60" cy="70" r="48" fill="var(--navy)"/>
      <text x="60" y="52" text-anchor="middle" font-family="Lato, sans-serif" font-weight="900" font-size="8.5" fill="#fff">WE ARE HERE</text>
      <text x="60" y="70" text-anchor="middle" font-family="Lato, sans-serif" font-weight="900" font-size="15" fill="#fff">FOR YOU</text>
      <text x="60" y="86" text-anchor="middle" font-family="Lato, sans-serif" font-weight="900" font-size="14" fill="var(--teal-light)">24 HOURS</text>
      <text x="60" y="100" text-anchor="middle" font-family="Lato, sans-serif" font-weight="900" font-size="9" fill="#fff">A DAY</text>
      <text font-family="Lato, sans-serif" font-weight="900" font-size="10.5" fill="var(--teal)" letter-spacing="1.2" transform="translate(-15 0)"><textPath href="#arc">EVERY DAY OF THE YEAR</textPath></text>
    </svg>
    <h2>OUR SERVICES</h2>
    <div class="copy">
      <p>At Trellis Animal Respite &amp; Home Care, our only goal is to support you in providing the very best care for your beloved companion in your own home.</p>
      <p>We work as a team to address the needs of your entire family. We come with no agenda and no prescribed plan, but rather follow your needs and wishes as they evolve and change over time. Some of the services we offer are:</p>
      <ul class="bullets">
        <li>Visiting and support</li>
        <li>Administration of medication &amp; fluids</li>
        <li>Overnight and respite care</li>
        <li>Check-ins, exercise and play</li>
        <li>Assistance evaluating pain, quality of life, and end of life choices</li>
        <li>Coordination of care with your vet and other care professionals</li>
        <li>Home cooked meals and treats</li>
        <li>Transportation and errand running</li>
        <li>Equipment and supplies</li>
        <li>Funerals and memorials</li>
        <li>Bereavement support</li>
      </ul>
    </div>
  </div>

  <div class="panel panel--3 team">
    <h3>OUR SKILLED TEAM MEMBERS CAN ALSO PROVIDE:</h3>
    <div class="skills">
      <ul>
        <li>Massage and TTouch</li>
        <li>Cold LASER Treatments</li>
        <li>Reiki</li>
        <li>Passive Range of Motion (PROM)</li>
        <li>Rehabilitation Support</li>
      </ul>
      <ul>
        <li>Grooming</li>
        <li>Essential Oils</li>
        <li>Bach Flower Essences</li>
        <li>Aroma Therapy</li>
        <li>Music Therapy</li>
        <li>Pet Therapy</li>
      </ul>
    </div>
    <h2>OUR TEAM</h2>
    <p class="lead">LEAD BY MIRIAM CASTELL, C.T. OUR INTERDISCIPLINARY TEAM INCLUDES:</p>
    <ul class="team-list">
      <li>Certified Thanatologist</li>
      <li>Certified Veterinary Technicians</li>
      <li>Interfaith Spiritual Advisor</li>
      <li>Certified Small Animal Massage Therapist</li>
      <li>Animal Care Specialists</li>
      <li>Hospice Assistants</li>
      <li>Client Care Coordinator</li>
    </ul>
    <svg class="panel-art" viewBox="0 0 234 548" preserveAspectRatio="none" aria-hidden="true">
      <path d="M0 548 L0 470 C60 420 150 380 234 380 L234 548 Z" fill="var(--navy)"/>
    </svg>
    <div class="photo" role="img" aria-label="Photo of a cream and grey cat lying down" style="left:20px;top:370px;width:214px;height:178px;clip-path:ellipse(70% 75% at 60% 80%);background:radial-gradient(ellipse at 60% 55%,#f4efe8 0%,#d8cfc4 45%,#9a8f84 80%)"></div>
  </div>
</section>

</body>
</html>
```